Business card update

Opening a subsidiary of my company in the USA and need to update my logo.
Updates

Reason: Give more time to a good design.

I made a mistake on my briefing. It's only the business card. Thanks for alerting me on the mistake.

All the best

Teodoro

Target Market(s)

We are an Executive Search company and our target audience are executives in large corporations.

Industry/Entity Type

Business

Requirements
Must have
• Keep the logo. In the US the company is called Delia Brunet Executive Search.

```html
<!DOCTYPE html>
<html lang="en">
<head>
<meta charset="utf-8">
<title>Delia Brunet Executive Search – Business Card</title>
<link rel="stylesheet" href="https://fonts.googleapis.com/css2?family=Quicksand:wght@300;400;500&display=swap">
<style>
  :root {
    --stage: #5b676b;
    --card-white: #ffffff;
    --card-teal: #48e5b1;
    --company-teal: #33c99c;
    --ink: #16201d;
    --phone-red: #d8231f;
  }
  * { margin: 0; padding: 0; box-sizing: border-box; }
  html, body {
    width: 1200px;
    height: 741px;
    overflow: hidden;
    background: var(--stage);
    font-family: "Quicksand", sans-serif;
  }
  .business-card {
    position: absolute;
    left: 80px;
    top: 68px;
    width: 1040px;
    height: 605px;
    background: var(--card-teal);
  }
  .card-header {
    position: absolute;
    left: 0; top: 0;
    width: 100%;
    height: 168px;
    background: var(--card-white);
  }
  .brand {
    position: absolute;
    right: 42px;
    top: 58px;
    display: flex;
    align-items: center;
    gap: 16px;
  }
  .brand-dot {
    width: 40px;
    height: 40px;
    border-radius: 50%;
    background: var(--card-teal);
  }
  .brand-name {
    font-weight: 500;
    font-size: 38px;
    color: var(--ink);
    line-height: 1;
  }
  .person-name {
    position: absolute;
    left: 55px;
    top: 196px;
    font-weight: 500;
    font-size: 41px;
    color: var(--card-white);
    line-height: 1;
  }
  .phone {
    position: absolute;
    left: 52px;
    top: 262px;
    display: flex;
    align-items: center;
    gap: 8px;
    font-weight: 500;
    font-size: 33px;
    color: var(--ink);
    line-height: 1;
  }
  .phone-icon { width: 28px; height: 28px; }
  .company-name {
    position: absolute;
    left: 46px;
    top: 410px;
    font-weight: 300;
    font-size: 70px;
    color: var(--company-teal);
    line-height: 1;
    white-space: nowrap;
  }
  .contact-block {
    position: absolute;
    top: 498px;
    font-style: normal;
    font-weight: 400;
    font-size: 25px;
    line-height: 35px;
    color: var(--ink);
  }
  .address { left: 48px; }
  .online { right: 42px; text-align: right; }
</style>
</head>
<body>
  <article class="business-card">
    <header class="card-header">
      <div class="brand">
        <span class="brand-dot" aria-hidden="true"></span>
        <span class="brand-name">Delia Brunet</span>
      </div>
    </header>

    <h1 class="person-name">Teodoro S. Brunet</h1>

    <p class="phone">
      <svg class="phone-icon" viewBox="0 0 24 24" aria-hidden="true">
        <path fill="var(--phone-red)" d="M6.6 10.8c1.4 2.8 3.8 5.1 6.6 6.6l2.2-2.2c.3-.3.7-.4 1-.2 1.1.4 2.3.6 3.6.6.6 0 1 .4 1 1V20c0 .6-.4 1-1 1C10.6 21 3 13.4 3 4c0-.6.4-1 1-1h3.5c.6 0 1 .4 1 1 0 1.3.2 2.5.6 3.6.1.3 0 .7-.2 1l-2.3 2.2z"/>
      </svg>
      305 555-0147
    </p>

    <h2 class="company-name">Delia Brunet Executive Search</h2>

    <address class="contact-block address">
      4820 Harbor Point Blvd Suite 310<br>
      Bayview FL 33190
    </address>

    <div class="contact-block online">
      www.dbexecutivesearch.com<br>
      tbrunet@dbexecutivesearch.com
    </div>
  </article>
</body>
</html>
```